Business Card - connecting 2 souls and beggining the journey of self discovery

Logo on the front
with tag line

On the back list of services and contact details

Seminars
workshops
Coaching
podcasts

Darren Whitlow
Health & Wellbeing Life Coach
0491 372 615
darren@brightcoreliving.example
brightcoreliving.example

Industry/Entity Type

Life Coaching

Contact Information for Business Card

I like the use of colour from the logo to be used. I'm not a fan of white.

Requirements
Must have
• My tagline: The journey home starts with you
Nice to have
• Use of colour that is in the Brightcore Living logo

```html
<!DOCTYPE html>
<html lang="en">
<head>
<meta charset="utf-8">
<title>Brightcore Living – Business Card</title>
<link rel="stylesheet" href="https://fonts.googleapis.com/css2?family=Montserrat:wght@500;600&family=Open+Sans:wght@400;600;700&display=swap">
<style>
  :root {
    --stage: #1c1c1d;
    --card: #3a3a3c;
    --card-edge: #444446;
    --ink: #f4f4f4;
    --muted: #c9c9cb;
    --accent-green: #8cc63f;
    --faint-disc: rgba(255, 255, 255, 0.08);
    --grad-purple: #9b5bb5;
    --grad-pink: #f0707a;
    --grad-orange: #f2a541;
    --grad-green: #8cc63f;
    --grad-teal: #2fb0a6;
  }
  * { box-sizing: border-box; margin: 0; padding: 0; }
  html, body {
    width: 1200px; height: 1000px; overflow: hidden;
    background: var(--stage);
  }
  .canvas {
    position: relative; width: 1200px; height: 1000px;
  }
  .card {
    position: absolute; left: 232px; width: 736px; height: 420px;
    background: var(--card);
    border-radius: 26px;
    overflow: hidden;
    box-shadow: inset 0 0 0 1px var(--card-edge);
  }
  .card--front { top: 60px; }
  .card--back { top: 520px; }

  /* Front side */
  .faint-disc {
    position: absolute; right: 48px; top: 40px;
    width: 336px; height: 336px; border-radius: 50%;
    background: var(--faint-disc);
  }
  .front-brand {
    position: absolute; left: 52px; bottom: 48px;
  }
  .brand-dot {
    width: 56px; height: 56px; border-radius: 50%;
    background: linear-gradient(135deg, var(--grad-purple), var(--grad-pink) 35%, var(--grad-orange) 60%, var(--grad-green) 80%, var(--grad-teal));
    margin-bottom: 16px;
  }
  .brand-name {
    font-family: "Montserrat", sans-serif; font-weight: 500;
    color: var(--ink); letter-spacing: -0.5px;
  }
  .front-brand .brand-name { font-size: 22px; }
  .tagline {
    font-family: "Open Sans", sans-serif; font-size: 14.5px;
    color: var(--accent-green); margin-top: 4px; letter-spacing: 0.3px;
  }

  /* Back side */
  .logo-disc {
    position: absolute; right: 44px; top: 40px;
    width: 340px; height: 340px; border-radius: 50%;
    background: linear-gradient(140deg, var(--grad-purple) 8%, var(--grad-pink) 35%, var(--grad-orange) 58%, var(--grad-green) 78%, var(--grad-teal) 96%);
  }
  .back-info {
    position: absolute; left: 52px; top: 70px;
  }
  .back-info .brand-name { font-size: 25px; }
  .services {
    font-family: "Open Sans", sans-serif; font-size: 15.5px;
    color: var(--muted); line-height: 1.3; margin-top: 28px; letter-spacing: 0.4px;
  }
  .person { margin-top: 44px; }
  .person-name {
    font-family: "Open Sans", sans-serif; font-weight: 700; font-size: 21px;
    color: var(--accent-green); text-transform: uppercase; letter-spacing: 0.3px;
  }
  .person-role {
    font-family: "Open Sans", sans-serif; font-weight: 600; font-size: 17px;
    color: var(--ink); margin-top: 1px;
  }
  .contacts {
    list-style: none; margin-top: 26px;
    font-family: "Open Sans", sans-serif; font-size: 14px; color: var(--ink);
  }
  .contacts li { display: flex; align-items: center; gap: 10px; height: 20px; }
  .contacts svg { width: 13px; height: 13px; fill: none; stroke: var(--accent-green); stroke-width: 2; }
  .contacts .web-domain { color: var(--accent-green); }
</style>
</head>
<body>
<main class="canvas">
  <section class="card card--front" aria-label="Card front">
    <div class="faint-disc" aria-hidden="true"></div>
    <div class="front-brand">
      <div class="brand-dot" aria-hidden="true"></div>
      <p class="brand-name">Brightcore Living</p>
      <p class="tagline">The journey home starts with you</p>
    </div>
  </section>

  <section class="card card--back" aria-label="Card back">
    <div class="back-info">
      <p class="brand-name">Brightcore Living</p>
      <p class="services">Seminars | Workshops<br>Coaching | Podcasts</p>
      <div class="person">
        <p class="person-name">Darren Whitlow</p>
        <p class="person-role">Life Coach</p>
      </div>
      <ul class="contacts">
        <li>
          <svg viewBox="0 0 14 14" aria-hidden="true"><rect x="3.5" y="1" width="7" height="12" rx="1.5"/><line x1="6" y1="10.5" x2="8" y2="10.5"/></svg>
          <span>0491 372 615</span>
        </li>
        <li>
          <svg viewBox="0 0 14 14" aria-hidden="true"><rect x="1" y="3" width="12" height="8.5" rx="1"/><polyline points="1,3.5 7,8 13,3.5"/></svg>
          <span>darren@brightcoreliving.example</span>
        </li>
        <li>
          <svg viewBox="0 0 14 14" aria-hidden="true"><circle cx="7" cy="7" r="6"/><ellipse cx="7" cy="7" rx="2.6" ry="6"/><line x1="1" y1="7" x2="13" y2="7"/></svg>
          <span>www.<span class="web-domain">brightcoreliving.example</span></span>
        </li>
      </ul>
    </div>
    <div class="logo-disc" aria-hidden="true"></div>
  </section>
</main>
</body>
</html>
```